Business card design Needed for new logo / Construction business, home extensions and new builds

We need a business card design using our new logo files which i will attach to this project :)

We are a small construction business specialising in home extensions, new builds and property development. We are very ambitious and would appreciate professional and elegant designs for our new business card.

Very serious about using the services on MakerQuarry and recently acquired our new logo from here :)

Please get involved, i will feedback when i can as i am very busy but can respond daily, thanks

Target Market(s)

People that want to build onto their houses, new building developments or adding too their existing property

Industry/Entity Type

Construction

Contact Information for Business Card

Renwick Tolliver Construction, Lionel Ashby (Managing Director), Tel 07822254961, email - info@renwick-tolliver, www.renwick-tolliver.co.uk

Colors

Designer to choose colors to be used in the design.

Requirements
Must have
• I like a deep grey on the back please. A lot of you have provided black from and back, try mixing things up a little. The black looks cool 😎 Thanks

```html
<!DOCTYPE html>
<html lang="en">
<head>
<meta charset="utf-8">
<title>Renwick Tolliver Construction – Business Card</title>
<link href="https://fonts.googleapis.com/css2?family=Open+Sans:wght@400;600;700&display=swap" rel="stylesheet">
<style>
  :root {
    --stage: #232323;
    --card: #222327;
    --card-deep: #1d1e21;
    --silver: #d9dadc;
    --silver-dark: #8e9094;
    --gold: #e0a42e;
    --gold-light: #f6cf6a;
    --text: #f2f2f2;
    --emboss: #2c2d31;
  }
  * { box-sizing: border-box; margin: 0; padding: 0; }
  html, body {
    width: 1200px; height: 780px; overflow: hidden;
    background: var(--stage);
    font-family: "Open Sans", Arial, sans-serif;
  }
  .stage {
    position: relative; width: 1200px; height: 780px;
  }
  .card {
    position: absolute; top: 235px;
    width: 540px; height: 310px;
    border-radius: 18px;
    background: var(--card);
    overflow: hidden;
    box-shadow: 0 12px 30px rgba(0,0,0,.55);
  }
  .card--back { left: 40px; background: var(--card-deep); }
  .card--front { left: 620px; }
  .edge-bands {
    position: absolute; left: 0; bottom: 0; width: 540px; height: 40px;
  }
  /* back */
  .back-name {
    position: absolute; left: 0; right: 0; top: 112px;
    text-align: center;
    font-weight: 700; font-size: 24px; letter-spacing: 1px;
    color: var(--emboss);
    text-transform: uppercase;
    line-height: 1.25;
  }
  /* front */
  .brand {
    position: absolute; left: 34px; top: 92px; width: 200px;
    display: flex; flex-direction: column; align-items: center; gap: 12px;
  }
  .brand-mark {
    width: 30px; height: 30px; background: var(--gold);
  }
  .brand-name {
    text-align: center; font-weight: 700; font-size: 17px;
    line-height: 1.3; letter-spacing: .5px; text-transform: uppercase;
    color: var(--silver);
  }
  .divider {
    position: absolute; left: 258px; top: 52px; width: 1px; height: 158px;
    background: linear-gradient(var(--silver), rgba(217,218,220,.2));
  }
  .contact {
    position: absolute; left: 284px; top: 48px;
    color: var(--text);
  }
  .person-name {
    font-weight: 700; font-size: 28px; line-height: 1.1;
    color: var(--silver);
  }
  .person-name .surname { color: var(--gold); }
  .person-role { font-size: 13px; margin-top: 2px; }
  .contact-list { list-style: none; margin-top: 26px; }
  .contact-list li {
    display: flex; align-items: center; gap: 9px;
    font-size: 13px; line-height: 22px;
  }
  .contact-list svg { width: 12px; height: 12px; flex: none; }
  .address {
    position: absolute; left: 0; right: 0; bottom: 52px;
    text-align: center; font-size: 13px; color: var(--text);
  }
</style>
</head>
<body>
<main class="stage">

  <section class="card card--back" aria-label="Card back">
    <p class="back-name">Renwick Tolliver<br>Construction</p>
    <svg class="edge-bands" viewBox="0 0 540 40" aria-hidden="true">
      <defs>
        <linearGradient id="goldBack" x1="0" y1="0" x2="0" y2="1">
          <stop offset="0" stop-color="#f6cf6a"/><stop offset=".5" stop-color="#e0a42e"/><stop offset="1" stop-color="#9c6a14"/>
        </linearGradient>
        <linearGradient id="silverBack" x1="0" y1="0" x2="0" y2="1">
          <stop offset="0" stop-color="#f4f5f6"/><stop offset=".5" stop-color="#c6c8cb"/><stop offset="1" stop-color="#7e8084"/>
        </linearGradient>
      </defs>
      <polygon points="0,28 300,28 292,40 0,40" fill="url(#goldBack)"/>
      <polygon points="318,16 540,16 540,40 306,40 318,22" fill="url(#silverBack)"/>
    </svg>
  </section>

  <section class="card card--front" aria-label="Card front">
    <div class="brand">
      <span class="brand-mark"></span>
      <p class="brand-name">Renwick Tolliver<br>Construction</p>
    </div>

    <span class="divider"></span>

    <div class="contact">
      <p class="person-name">Lionel <span class="surname">Ashby</span></p>
      <p class="person-role">Managing Director</p>
      <ul class="contact-list">
        <li>
          <svg viewBox="0 0 24 24" fill="var(--gold)" aria-hidden="true"><path d="M6.6 10.8a15 15 0 0 0 6.6 6.6l2.2-2.2a1 1 0 0 1 1-.25 11.4 11.4 0 0 0 3.6.57 1 1 0 0 1 1 1V20a1 1 0 0 1-1 1A17 17 0 0 1 3 4a1 1 0 0 1 1-1h3.5a1 1 0 0 1 1 1c0 1.25.2 2.45.57 3.57a1 1 0 0 1-.25 1z"/></svg>
          0782 225 4961
        </li>
        <li>
          <svg viewBox="0 0 24 24" fill="none" stroke="var(--gold)" stroke-width="2.4" aria-hidden="true"><circle cx="12" cy="12" r="9.5"/><path d="M2.5 12h19M12 2.5c3 3 3 16 0 19M12 2.5c-3 3-3 16 0 19"/></svg>
          info@renwick-tolliver.co.uk
        </li>
        <li>
          <svg viewBox="0 0 24 24" fill="none" stroke="var(--gold)" stroke-width="2.4" aria-hidden="true"><rect x="2.5" y="5" width="19" height="14" rx="1.5"/><path d="M3 6l9 7 9-7"/></svg>
          www.renwick-tolliver.co.uk
        </li>
      </ul>
    </div>

    <p class="address">Ashcombe Lane, Westmere Harbury, HB4 7QN</p>

    <svg class="edge-bands" viewBox="0 0 540 40" aria-hidden="true">
      <defs>
        <linearGradient id="goldFront" x1="0" y1="0" x2="0" y2="1">
          <stop offset="0" stop-color="#f6cf6a"/><stop offset=".5" stop-color="#e0a42e"/><stop offset="1" stop-color="#9c6a14"/>
        </linearGradient>
        <linearGradient id="silverFront" x1="0" y1="0" x2="0" y2="1">
          <stop offset="0" stop-color="#f4f5f6"/><stop offset=".5" stop-color="#c6c8cb"/><stop offset="1" stop-color="#7e8084"/>
        </linearGradient>
      </defs>
      <polygon points="0,28 300,28 292,40 0,40" fill="url(#goldFront)"/>
      <polygon points="318,16 540,16 540,40 306,40 318,22" fill="url(#silverFront)"/>
    </svg>
  </section>

</main>
</body>
</html>
```